Diverse, up-scale salon needs eye-catching, unique business cards.

We are looking for a unique business card design for our stylist but that can also be multi functional and used for appointment reminder and referrals. I will need a design in a format that I can modify names and titles going forward. In the past we have had a dark background with the logo on one side, and stylist and contact information on the other but we are open to all ideas. I have included our mission statement as well as branded colors below. The statement doesn't need to go on the card, it's just a reference for target market. We need space for the stylists name, title, instagram handle and then the salons phone number, website and address. I am also open to adding a spot for a qr code linked to the stylist instagram or the salon booking link.

primary brand colors:
#333333 #233415 #36502a #93874a #000000
Mission statement:
Vessolin Hair Studio, a high-end salon located in the lively Downtown Farmington, Michigan, is committed to providing exceptional services in a welcoming and relaxed environment to meet the needs of our diverse clientele.
Our salon specializes in contemporary custom haircuts, coloring, extensions, and barbering and beard grooming services. Our team of skilled stylists is passionate and inventive in their hair styling techniques. At the heart of our salon are values centered on quality, innovation, creativity, and above all, comfort. These core values are evident in every appointment across our customizable array of services.
Our goal is to establish a benchmark for exceptional hair care for every human.
Website: www.vessolinhairstudio.example
instagram: @vessolinhairstudio
address: 41782 Pelham Crest Rd, Farmington MI
phone: 555-555-0147

Industry/Entity Type

Hair Salon

Contact Information for Business Card

Stylist name, title, phone, instagram, website, address, (optional qr code)

Requirements
Should not have
• Does not need mission statement on the card.

```html
<!DOCTYPE html>
<html lang="en">
<head>
<meta charset="utf-8">
<title>Vessolin Hair Studio — Business Cards</title>
<link href="https://fonts.googleapis.com/css2?family=Montserrat:wght@400;500&family=Nunito+Sans:wght@400&family=Allura&display=swap" rel="stylesheet">
<style>
  :root {
    --backdrop: #1b1b1b;
    --card: #222222;
    --card-edge: #2a2a2a;
    --gold: #93874a;
    --ink-light: #d9d9d9;
    --ink-soft: #bdbdbd;
  }
  html, body {
    margin: 0;
    padding: 0;
    width: 1200px;
    height: 939px;
    overflow: hidden;
    background: var(--backdrop);
  }
  .canvas {
    position: relative;
    width: 1200px;
    height: 939px;
  }
  .card {
    position: absolute;
    width: 520px;
    height: 297px;
    background: var(--card);
    border-radius: 14px;
    box-shadow: 0 18px 40px rgba(0,0,0,.55);
    border: 1px solid var(--card-edge);
  }
  .card__frame {
    position: absolute;
    inset: 12px;
    border: 1px solid var(--gold);
    border-radius: 10px;
  }
  /* Front */
  .card--front { left: 110px; top: 90px; }
  .front__wordmark {
    position: absolute;
    inset: 0;
    display: flex;
    align-items: center;
    justify-content: center;
    font-family: "Montserrat", sans-serif;
    font-weight: 500;
    font-size: 26px;
    letter-spacing: .22em;
    text-transform: uppercase;
    color: var(--gold);
    text-align: center;
    line-height: 1.5;
  }
  /* Back */
  .card--back { left: 570px; top: 500px; }
  .badge {
    position: absolute;
    left: 58px;
    top: 58px;
    width: 150px;
    height: 150px;
    border: 2px solid var(--gold);
    border-radius: 50%;
    display: flex;
    align-items: center;
    justify-content: center;
    text-align: center;
    font-family: "Montserrat", sans-serif;
    font-weight: 500;
    font-size: 13px;
    letter-spacing: .18em;
    line-height: 1.6;
    text-transform: uppercase;
    color: var(--gold);
  }
  .stylist {
    position: absolute;
    left: 262px;
    top: 42px;
  }
  .stylist__name {
    font-family: "Allura", cursive;
    font-size: 46px;
    line-height: 1;
    color: var(--ink-light);
    margin: 0;
  }
  .stylist__title {
    font-family: "Nunito Sans", sans-serif;
    font-size: 13px;
    color: var(--ink-soft);
    margin: 2px 0 0 6px;
  }
  .stylist__rule {
    width: 30px;
    height: 2px;
    background: var(--gold);
    margin: 10px 0 10px 6px;
  }
  .contact {
    list-style: none;
    margin: 0 0 0 6px;
    padding: 0;
    font-family: "Nunito Sans", sans-serif;
    font-size: 12px;
    line-height: 1.75;
    color: var(--ink-soft);
  }
  .address {
    position: absolute;
    left: 12px;
    right: 12px;
    bottom: 12px;
    display: flex;
    align-items: center;
    transform: translateY(50%);
    font-family: "Montserrat", sans-serif;
    font-size: 9.5px;
    letter-spacing: .14em;
    text-transform: uppercase;
    color: var(--ink-light);
    white-space: nowrap;
  }
  .address__text {
    background: var(--card);
    padding: 0 6px;
    margin: 0 auto;
  }
</style>
</head>
<body>
<main class="canvas">
  <section class="card card--front" aria-label="Business card front">
    <div class="card__frame"></div>
    <div class="front__wordmark">Vessolin<br>Hair Studio</div>
  </section>

  <section class="card card--back" aria-label="Business card back">
    <div class="card__frame"></div>
    <div class="badge">Vessolin<br>Hair<br>Studio</div>
    <div class="stylist">
      <p class="stylist__name">Marcus Hale</p>
      <p class="stylist__title">Owner / Hair Stylist</p>
      <div class="stylist__rule"></div>
      <ul class="contact">
        <li>555-555-0147</li>
        <li>hello@vessolinhairstudio.example</li>
        <li>www.vessolinhairstudio.example</li>
        <li>@vessolinhairstudio</li>
      </ul>
    </div>
    <div class="address"><span class="address__text">41782 Pelham Crest Rd, Larkmoor Vale</span></div>
  </section>
</main>
</body>
</html>
```